Private Investment Firm Needs PowerPoint Presentation Template

Design PowerPoint template, take Pinebrook-submitted rough presentation draft, and drop it into new template. See attached Project Brief file for more detail.
Updates

Some decent designs have been submitted but they seem to lack the understanding of our target markets. I am hopeful that more time and feedback will result in better results.

Target Market(s)

Private company owners and intermediaries.

Font styles to use
Serif

Colors
3176b5

Requirements
Must have
• See attached Project Brief.
Nice to have
Should not have
• No B2C fluff--this is a B2B project.

```html
<!DOCTYPE html>
<html lang="en">
<head>
<meta charset="utf-8">
<title>Introduction – Pinebrook Capital</title>
<link href="https://fonts.googleapis.com/css2?family=Montserrat:wght@400;500;700&display=swap" rel="stylesheet">
<style>
  :root {
    --page-bg: #e9e9ec;
    --slide-top: #eeeef1;
    --slide-bottom: #ffffff;
    --charcoal: #58595b;
    --brand-blue: #1a6bb5;
    --band-top: #0b63b0;
    --band-bottom: #2596d0;
    --body-text: #444548;
    --white: #ffffff;
  }
  * { box-sizing: border-box; margin: 0; padding: 0; }
  html, body {
    width: 1200px; height: 770px; overflow: hidden;
    background: var(--page-bg);
    font-family: "Montserrat", sans-serif;
  }
  .slide {
    position: absolute; left: 0; top: 47px;
    width: 1200px; height: 675px; overflow: hidden;
    background: linear-gradient(160deg, var(--slide-top) 0%, var(--slide-bottom) 70%);
  }
  .slide-shapes { position: absolute; inset: 0; }
  .slide-title {
    position: absolute; left: 0; width: 1110px; top: 76px;
    text-align: center; font-size: 36px; font-weight: 700;
    letter-spacing: 1px; color: var(--brand-blue);
  }
  .title-rule {
    position: absolute; left: 529px; top: 127px;
    width: 58px; height: 4px; border-radius: 2px; background: var(--brand-blue);
  }
  .bullets { position: absolute; left: 0; top: 0; list-style: none; }
  .bullet {
    position: absolute; left: 155px; width: 846px;
    font-size: 19.5px; line-height: 22.4px; color: var(--body-text);
    text-align: justify; text-align-last: left;
  }
  .bullet::before {
    content: ""; position: absolute; left: -30px; top: 3px;
    width: 7px; height: 7px; border-radius: 50%; background: var(--brand-blue);
  }
  .checks { list-style: none; }
  .check {
    position: absolute; left: 49px; white-space: nowrap;
  }
  .check::before {
    content: "\2713"; position: absolute; left: -20px; top: 0;
    font-size: 15px; color: var(--brand-blue);
  }
  .brand {
    position: absolute; left: 121px; top: 597px;
    display: flex; align-items: center; gap: 10px;
  }
  .brand-dot { width: 30px; height: 30px; border-radius: 50%; background: var(--brand-blue); }
  .brand-name {
    font-size: 17px; font-weight: 500; letter-spacing: 1px;
    color: var(--brand-blue); text-transform: uppercase;
  }
  .site-url {
    position: absolute; left: 598px; width: 300px; top: 599px;
    text-align: center; font-size: 18px; color: #222;
  }
  .site-url strong { color: var(--brand-blue); font-weight: 700; }
  .page-number {
    position: absolute; left: 1096px; top: 601px;
    font-size: 15px; font-weight: 700; color: var(--white);
  }
</style>
</head>
<body>
  <section class="slide">
    <svg class="slide-shapes" width="1200" height="675" viewBox="0 0 1200 675">
      <defs>
        <linearGradient id="bandFill" x1="0" y1="0" x2="0" y2="1">
          <stop offset="0" stop-color="var(--band-top)"/>
          <stop offset="1" stop-color="var(--band-bottom)"/>
        </linearGradient>
      </defs>
      <polygon points="0,0 106,0 0,447" fill="var(--charcoal)"/>
      <polygon points="1200,0 1200,675 983,675" fill="url(#bandFill)"/>
    </svg>

    <h1 class="slide-title">INTRODUCTION</h1>
    <div class="title-rule"></div>

    <ul class="bullets">
      <li class="bullet" style="top:164px">Private company owners have traditionally considered two capital raising options
        <ul class="checks">
          <li class="check" style="top:32px">Borrow from a local bank, or</li>
          <li class="check" style="top:62px">Sell most or all of the company to a change- of-control investor (aka Buyout firm)</li>
        </ul>
      </li>
      <li class="bullet" style="top:276px">An alternative most have not considered is the raising of Non-Control Capital, or capital that is invested into the business yet allows those same owners to retain controlling interest in their company</li>
      <li class="bullet" style="top:372px; width:800px">Non-Control Capital is not appropriate for every private company owner but neither is a Change-of-Control sale</li>
      <li class="bullet" style="top:445px; width:845px">The key is to determine what the business and owners require, and then partner with an investor best aligned with those needs so that long-term company growth, and personal goals, can both be achieved</li>
    </ul>

    <div class="brand">
      <span class="brand-dot"></span>
      <span class="brand-name">Pinebrook Capital</span>
    </div>
    <p class="site-url">www.<strong>pinebrookcapital</strong>.com</p>
    <p class="page-number">1.</p>
  </section>
</body>
</html>
```